Bramblewood Card Company Business Cards

We are a trading card store with Glimmorax, sports and other TCG cards, we need a business card design that encompasses a clean cut, modern style with a retro flare. website is bramblewoodcardco.com for reference. Can utilize a comic book era feel or a more modern outdoor feel to utilize the "Pacific Northwest" elements of tress, mountains, etc.

Industry/Entity Type

Trading cards and collectibles

Contact Information for Business Card

business name, email address, phone number, name, owner job title

Font styles to use
Sans Serif

```html
<!DOCTYPE html>
<html lang="en">
<head>
<meta charset="utf-8">
<title>Bramblewood Card Company – Business Card</title>
<link rel="stylesheet" href="https://fonts.googleapis.com/css2?family=Montserrat:wght@400;500;700&display=swap">
<style>
  :root {
    --backdrop: #d5d9da;
    --paper: #f7f7f5;
    --cyan: #10b6da;
    --cyan-deep: #0f9fc0;
    --ink: #3a3d40;
    --ink-soft: #55595d;
    --rule: #c9cccd;
  }
  * { box-sizing: border-box; margin: 0; padding: 0; }
  html, body {
    width: 1200px; height: 829px; overflow: hidden;
    background: var(--backdrop);
    font-family: "Montserrat", sans-serif;
  }
  .sheet {
    width: 1200px; height: 829px;
    display: flex; align-items: center; justify-content: center; gap: 60px;
  }
  .card {
    width: 525px; height: 300px;
    position: relative;
    box-shadow: 0 14px 30px rgba(0,0,0,0.14);
  }
  .card-front { background: var(--paper); border-bottom: 3px solid var(--cyan); }
  .card-back { background: var(--cyan); display: flex; align-items: center; justify-content: center; }

  .identity {
    position: absolute; right: 292px; top: 118px;
    text-align: right;
    white-space: nowrap;
  }
  .person-name {
    color: var(--cyan);
    font-weight: 700; font-size: 21px; letter-spacing: 1px;
    text-transform: uppercase; line-height: 1.1;
  }
  .person-role {
    color: var(--ink-soft);
    font-weight: 400; font-size: 13px; margin-top: 3px;
  }
  .divider {
    position: absolute; left: 248px; top: 112px;
    width: 1px; height: 86px; background: var(--rule);
  }
  .contact {
    position: absolute; left: 264px; top: 110px;
    color: var(--ink); font-size: 12.5px; line-height: 1.45;
    list-style: none;
    white-space: nowrap;
  }
  .contact li { display: flex; align-items: center; gap: 6px; }
  .contact .address { padding-left: 16px; }
  .contact svg { width: 10px; height: 10px; flex: none; fill: var(--cyan); }

  .brand-name {
    color: var(--ink);
    font-weight: 700; font-size: 26px; letter-spacing: 1px;
    text-transform: uppercase; text-align: center; line-height: 1.2;
    display: flex; align-items: center; gap: 14px;
  }
  .brand-dot {
    width: 18px; height: 18px; border-radius: 50%;
    background: var(--ink); flex: none;
  }
</style>
</head>
<body>
<main class="sheet">
  <section class="card card-front" aria-label="Business card front">
    <div class="identity">
      <h1 class="person-name">Dorian Pell</h1>
      <p class="person-role">CEO/Founder</p>
    </div>
    <div class="divider"></div>
    <ul class="contact">
      <li class="address">P.O. Box 3178 Fern Road</li>
      <li class="address">Cedar Hollow WA 98671</li>
      <li>
        <svg viewBox="0 0 10 10" aria-hidden="true"><path d="M2 0.5 L3.6 0.5 L4.3 2.8 L3.2 3.6 Q4.2 5.8 6.4 6.8 L7.2 5.7 L9.5 6.4 L9.5 8 Q9.5 9.5 8 9.5 Q0.5 9 0.5 2 Q0.5 0.5 2 0.5 Z"/></svg>
        (555) 014 2736
      </li>
      <li>
        <svg viewBox="0 0 10 10" aria-hidden="true"><path d="M0.5 2 H9.5 V8 H0.5 Z M0.5 2 L5 5.5 L9.5 2" stroke="#f7f7f5" stroke-width="0.8"/></svg>
        info@bramblewoodcardco.com
      </li>
      <li>
        <svg viewBox="0 0 10 10" aria-hidden="true"><circle cx="5" cy="5" r="4.5"/><path d="M0.5 5 H9.5 M5 0.5 Q2.5 5 5 9.5 M5 0.5 Q7.5 5 5 9.5" stroke="#f7f7f5" stroke-width="0.6" fill="none"/></svg>
        www.bramblewoodcardco.com
      </li>
    </ul>
  </section>

  <section class="card card-back" aria-label="Business card back">
    <div class="brand-name">
      <span class="brand-dot"></span>
      <span>Bramblewood<br>Card Company</span>
    </div>
  </section>
</main>
</body>
</html>
```